Help our Sugar Loom find our winning design! We're looking for a business card....

We’re a Sugar Loom in NY specializing in custom-made cakes and unique desserts.
Our cakes combine flavor and art, each designed to match customer’s special event and theme.
We’d like a unique business card with a clean design that will combine French chic and artistic look & feel.
We’d like to differentiate ourselves from standard bakeries, please don’t offer cupcake images :-)
Our logo is peach-pink and brown and we’d love to use these colors ( . Another color that can be added is gold - or feel free to suggest!

Target Market(s)

Women, ages 25-55

Industry/Entity Type

Boutique

Contact Information for Business Card

Text on card:
Logo
Sugar Loom by Dana Welch

www.sugarloomsweets.com
hello@sugarloom.com
(516) 555-0147
F – sugarloomnyc
IG - sugarloom_ny

Font styles to use
Sans Serif
Script

Requirements
Must have
• Logo
• Clean look
• French chic and artistic look & feel.
Nice to have
• Damask pattern
Should not have
• Cupcake images

```html
<!DOCTYPE html>
<html lang="en">
<head>
<meta charset="utf-8">
<title>Sugar Loom – Business Card</title>
<link href="https://fonts.googleapis.com/css2?family=Crimson+Text:wght@400&display=swap" rel="stylesheet">
<style>
  :root {
    --backdrop: #d9d9d9;
    --card: #ffffff;
    --peach: #e8a397;
    --peach-soft: #f7e4e0;
    --brown: #3b2a26;
    --gold: #c9a237;
    --gold-light: #f2dc84;
    --damask: #f1f1f1;
  }
  * { box-sizing: border-box; margin: 0; padding: 0; }
  html, body { width: 1200px; height: 852px; overflow: hidden; }
  body { background: var(--backdrop); position: relative; }

  .card {
    position: absolute;
    width: 520px;
    height: 297px;
    border-radius: 18px;
    background: var(--card);
    overflow: hidden;
    box-shadow: 0 6px 18px rgba(0,0,0,0.18);
  }
  .card--front { left: 50px; top: 190px; }
  .card--back { left: 630px; top: 365px; }

  .damask-fill {
    position: absolute; inset: 0;
    background: linear-gradient(135deg, var(--damask), #fafafa 50%, var(--damask));
  }
  .ribbon-band {
    position: absolute; left: 0; right: 0; top: 140px; height: 34px;
    background: var(--peach);
  }
  .name-plate {
    position: absolute; left: 110px; top: 86px; width: 300px; height: 140px;
    background: var(--card);
    border: 2px solid var(--peach);
    border-radius: 60px;
    display: flex; align-items: center; justify-content: center;
  }
  .brand-name {
    font-family: "Crimson Text", serif;
    font-weight: 400;
    color: var(--brown);
    font-size: 40px;
    line-height: 1;
    white-space: nowrap;
  }

  .flourish {
    position: absolute;
    background: radial-gradient(ellipse at center, var(--peach-soft), rgba(255,255,255,0) 70%);
  }
  .flourish--left { left: 10px; top: 60px; width: 110px; height: 160px; }
  .flourish--right { right: 10px; top: 0; width: 170px; height: 90px; }
  .back-name {
    position: absolute; left: 0; right: 0; top: 0; height: 150px;
    display: flex; align-items: center; justify-content: center;
  }
  .gold-rule {
    position: absolute; left: 0; right: 0; top: 150px; height: 5px;
    background: linear-gradient(90deg, var(--gold), var(--gold-light), var(--gold));
  }
  .back-panel {
    position: absolute; left: 0; right: 0; top: 155px; bottom: 0;
    background: var(--peach);
  }
  .contact-list, .social-list {
    position: absolute; list-style: none;
    font-family: "Crimson Text", serif;
    color: var(--brown);
    font-size: 15px;
    line-height: 1.3;
  }
  .contact-list { left: 26px; bottom: 22px; }
  .social-list { right: 26px; top: 20px; }
  .contact-list li, .social-list li { display: flex; align-items: center; gap: 10px; white-space: nowrap; }
  .icon { width: 12px; height: 12px; flex: none; }
  .social-mark {
    width: 11px; height: 11px; border-radius: 2px;
    background: var(--brown); flex: none;
  }
</style>
</head>
<body>

<section class="card card--front" aria-label="Card front">
  <div class="damask-fill" role="img" aria-label="Faint white damask pattern background"></div>
  <div class="ribbon-band"></div>
  <div class="name-plate">
    <span class="brand-name">Sugar Loom</span>
  </div>
</section>

<section class="card card--back" aria-label="Card back">
  <div class="flourish flourish--left" role="img" aria-label="Faint pink floral flourish ornament"></div>
  <div class="flourish flourish--right" role="img" aria-label="Faint pink floral flourish ornament"></div>
  <div class="back-name">
    <span class="brand-name">Sugar Loom</span>
  </div>
  <div class="gold-rule"></div>
  <div class="back-panel">
    <ul class="social-list">
      <li><span class="social-mark"></span>sugarloomnyc</li>
      <li><span class="social-mark"></span>sugarloom_ny</li>
    </ul>
    <ul class="contact-list">
      <li>
        <svg class="icon" viewBox="0 0 12 12" aria-hidden="true"><path d="M2 1h3l1 3-1.5 1a6 6 0 0 0 2.5 2.5L8 6l3 1v3a1 1 0 0 1-1 1A9 9 0 0 1 1 2a1 1 0 0 1 1-1z" fill="#3b2a26"/></svg>
        (516) 555-0147
      </li>
      <li>
        <svg class="icon" viewBox="0 0 12 12" aria-hidden="true"><circle cx="6" cy="6" r="5" fill="none" stroke="#3b2a26" stroke-width="1.2"/><path d="M1 6h10M6 1c2 2 2 8 0 10M6 1c-2 2-2 8 0 10" fill="none" stroke="#3b2a26" stroke-width="1"/></svg>
        www.sugarloomsweets.com
      </li>
      <li>
        <svg class="icon" viewBox="0 0 12 12" aria-hidden="true"><rect x="0.5" y="2" width="11" height="8" fill="#3b2a26"/><path d="M0.5 2l5.5 4.5L11.5 2" fill="none" stroke="#e8a397" stroke-width="1"/></svg>
        hello@sugarloom.com
      </li>
    </ul>
  </div>
</section>

</body>
</html>
```